Mainpage design for a catalog service
To designers:
The ads on the left and right are not fixed size ads. They may vary in size and shape. If you take a look at the attached picture for kvelda.no you will notice that the actual ad is defined in the background and it takes up all the available space.
RT/PKW/HN Team
Please feel free to use free pictures which are available on the internet in the design. Preferably we want a design with least amount of pictures.
We are looking for simplify and to make a fresher design for the site. The ads on the left and right are floating on the background. You are free to be creative for these ads. they don't need to be aligned vertically with the design or to be constraint to the given space in the prototype picture

```html
<!DOCTYPE html>
<html lang="en">
<head>
<meta charset="utf-8">
<title>KATALOGEN.no – Catalog</title>
<link rel="stylesheet" href="https://fonts.googleapis.com/css2?family=Arimo:wght@400;700&display=swap">
<style>
:root{
  --green-dark:#2f5a0c;
  --green:#5f9a1f;
  --green-light:#8fc13f;
  --white:#ffffff;
  --muted:#666;
  --ad-text:#555;
  --footer-top:#4a4a4a;
  --footer-bottom:#222;
  --social:#4a7fb5;
}
*{margin:0;padding:0;box-sizing:border-box}
html,body{width:1200px;height:778px;overflow:hidden}
body{
  font-family:"Arimo",Arial,sans-serif;
  position:relative;
  background:linear-gradient(90deg,#274a08 0%,#4f8a16 18%,#629f24 50%,#4f8a16 82%,#274a08 100%);
}
.top-ad{position:absolute;left:187px;top:0;width:821px;height:113px;background:var(--white);
  display:flex;align-items:center;justify-content:center;font-size:26px;color:var(--ad-text)}
.nav{position:absolute;left:187px;top:120px;width:821px;height:31px;
  background:linear-gradient(#6d9f2a,#3f6e12);border:2px solid var(--white);
  display:flex;align-items:center;padding:0 8px;font-size:11px;color:var(--white)}
.nav a{color:var(--white);text-decoration:none;padding:5px 16px}
.nav a.active{background:linear-gradient(#9cc95a,#6f9f30);border-radius:2px}
.nav .lang{margin-left:auto}
.hero{position:absolute;left:187px;top:163px;width:821px;height:132px;
  background:linear-gradient(#84b63b,#4d8216);border-radius:6px;border:1px solid #a9d169}
.brand{position:absolute;left:12px;top:18px;display:flex;flex-direction:column;align-items:flex-start;gap:8px}
.brand-mark{width:70px;height:70px;border-radius:50%;background:#e9e9e9}
.brand-name{font-size:18px;font-weight:700;color:var(--white)}
.hero h1{position:absolute;left:198px;top:20px;font-size:19px;color:var(--white);font-weight:700}
.hero p{position:absolute;left:198px;top:48px;width:370px;font-size:10.5px;line-height:13px;color:var(--white)}
.search{position:absolute;display:flex;gap:8px}
.search .field{background:var(--white);border:1px solid #bbb;border-radius:2px;color:#aaa;font-size:10px;padding:4px 6px}
.search .go{background:linear-gradient(#ddd,#999);border-radius:2px;width:34px;display:flex;align-items:center;justify-content:center}
.hero .search{left:617px;top:67px}
.hero .field{width:156px;height:22px}
.side-ad{position:absolute;width:142px;height:195px;background:var(--white);
  display:flex;align-items:center;justify-content:center;font-size:20px;font-weight:700;color:var(--ad-text)}
.content{position:absolute;left:336px;top:305px;width:528px;height:405px;background:var(--white);border-radius:6px}
.cat-head{position:absolute;left:5px;top:7px;width:516px;height:43px;border-radius:8px;
  background:linear-gradient(#8cbf3f,#4d8216);color:var(--white);font-size:19px;font-weight:700;padding:10px 14px}
.cat-grid{position:absolute;left:19px;top:70px;display:grid;grid-template-columns:repeat(4,130px);row-gap:22px}
.cat h2{font-size:11px;font-weight:700;color:var(--green);border-bottom:1px solid #cfdcbc;width:100px;padding-bottom:3px;margin-bottom:4px}
.cat li{list-style:none;font-size:9.5px;line-height:15.5px;color:var(--muted);padding-left:8px}
.cat li::before{content:"- ";}
.content .search{left:324px;top:372px}
.content .field{width:156px;height:20px}
.footer{position:absolute;left:0;top:715px;width:1200px;height:63px;background:linear-gradient(var(--footer-top),var(--footer-bottom))}
.footer small{position:absolute;left:192px;top:42px;font-size:10px;color:#ddd}
.social{position:absolute;left:884px;top:14px;display:flex;gap:14px}
.social span{width:32px;height:32px;border-radius:4px;background:var(--social);border:1px solid rgba(255,255,255,.35)}
</style>
</head>
<body>
<div class="top-ad">Your AD</div>
<nav class="nav">
  <a class="active">Home</a><a>About Us</a><a>Services</a><a>Product</a><a>Contact Us</a>
  <span class="lang">English ▼</span>
</nav>
<section class="hero">
  <div class="brand"><span class="brand-mark"></span><span class="brand-name">KATALOGEN.no</span></div>
  <h1>Welcome to KATALOGEN.no</h1>
  <p>Lorem ipsum dolor is amet,consectetur adipiscing elit.Integer dictum,magna id aliquam aliquet,nulla turpis temporvellus vitae sollicitudinvis vitc ut neque ut at felis a neque sollicitudin egestas.</p>
  <div class="search"><div class="field">Search</div><div class="go"><svg width="10" height="8"><path d="M0 4h8M5 1l3 3-3 3" stroke="#fff" stroke-width="1.5" fill="none"/></svg></div></div>
</section>
<div class="side-ad" style="left:187px;top:305px">AD</div>
<div class="side-ad" style="left:187px;top:511px">AD</div>
<div class="side-ad" style="left:871px;top:305px">AD</div>
<div class="side-ad" style="left:871px;top:511px">AD</div>
<main class="content">
  <div class="cat-head">Categories</div>
  <div class="cat-grid">
    <div class="cat"><h2>Lorem Ipsum ›</h2><ul><li>Lorem Ipsum</li><li>Duis Aptiue</li><li>Dolor Si Amet</li><li>Lorem Ipsum</li><li>Duis Aptiue</li><li>Dolor Si Amet</li></ul></div>
    <div class="cat"><h2>Lorem Ipsum ›</h2><ul><li>Lorem Ipsum</li><li>Duis Aptiue</li><li>Dolor Si Amet</li><li>Lorem Ipsum</li><li>Duis Aptiue</li><li>Dolor Si Amet</li></ul></div>
    <div class="cat"><h2>Lorem Ipsum ›</h2><ul><li>Lorem Ipsum</li><li>Duis Aptiue</li><li>Dolor Si Amet</li><li>Lorem Ipsum</li><li>Duis Aptiue</li><li>Dolor Si Amet</li></ul></div>
    <div class="cat"><h2>Lorem Ipsum ›</h2><ul><li>Lorem Ipsum</li><li>Duis Aptiue</li><li>Dolor Si Amet</li><li>Lorem Ipsum</li><li>Duis Aptiue</li><li>Dolor Si Amet</li></ul></div>
    <div class="cat"><h2>Lorem Ipsum ›</h2><ul><li>Lorem Ipsum</li><li>Duis Aptiue</li><li>Dolor Si Amet</li><li>Lorem Ipsum</li><li>Duis Aptiue</li><li>Dolor Si Amet</li></ul></div>
    <div class="cat"><h2>Lorem Ipsum ›</h2><ul><li>Lorem Ipsum</li><li>Duis Aptiue</li><li>Dolor Si Amet</li><li>Lorem Ipsum</li><li>Duis Aptiue</li><li>Dolor Si Amet</li></ul></div>
    <div class="cat"><h2>Lorem Ipsum ›</h2><ul><li>Lorem Ipsum</li><li>Duis Aptiue</li><li>Dolor Si Amet</li><li>Lorem Ipsum</li><li>Duis Aptiue</li><li>Dolor Si Amet</li></ul></div>
    <div class="cat"><h2>Lorem Ipsum ›</h2><ul><li>Lorem Ipsum</li><li>Duis Aptiue</li><li>Dolor Si Amet</li><li>Lorem Ipsum</li><li>Duis Aptiue</li><li>Dolor Si Amet</li></ul></div>
  </div>
  <div class="search"><div class="field">Search</div><div class="go"><svg width="10" height="8"><path d="M0 4h8M5 1l3 3-3 3" stroke="#fff" stroke-width="1.5" fill="none"/></svg></div></div>
</main>
<footer class="footer">
  <small>Copyright © 2010-2013, KATALOGEN.no</small>
  <div class="social" role="img" aria-label="Social network links"><span></span><span></span><span></span></div>
</footer>
</body>
</html>
```